Working Capital graphics

Our business advisory firm requires 9 images to be re-created and improved in the branding of our business.

The 9 images have been uploaded below and the colours and branding of the business can be found at the website www.tallowmereadvisory.com.au

```html
<!DOCTYPE html>
<html lang="en">
<head>
<meta charset="utf-8">
<title>Working Capital</title>
<link rel="stylesheet" href="https://fonts.googleapis.com/css2?family=Montserrat:wght@600;700&display=swap">
<style>
  :root {
    --bg: #ffffff;
    --hub: #f09d45;
    --node: #55a8dc;
    --ink: #111111;
  }
  html, body {
    margin: 0;
    padding: 0;
    overflow: hidden;
    background: var(--bg);
  }
  .canvas {
    width: 1200px;
    height: 1000px;
    display: block;
  }
  .hub-circle { fill: var(--hub); }
  .node-circle { fill: var(--node); }
  .hub-label {
    font-family: "Montserrat", Arial, sans-serif;
    font-weight: 700;
    font-size: 62px;
    fill: var(--ink);
    text-anchor: middle;
  }
  .node-label {
    font-family: "Montserrat", Arial, sans-serif;
    font-weight: 700;
    font-size: 22px;
    fill: var(--ink);
    text-anchor: middle;
  }
</style>
</head>
<body>
<svg class="canvas" viewBox="0 0 1200 1000" xmlns="http://www.w3.org/2000/svg" aria-labelledby="diagram-title">
  <title id="diagram-title">Working Capital drivers</title>

  <g class="hub">
    <circle class="hub-circle" cx="588" cy="508" r="188"/>
    <text class="hub-label" x="588" y="493">Working</text>
    <text class="hub-label" x="588" y="575">Capital</text>
  </g>

  <g class="node">
    <circle class="node-circle" cx="587" cy="144" r="99"/>
    <text class="node-label" x="587"><tspan x="587" y="111">Supply</tspan><tspan x="587" y="150">Chain</tspan><tspan x="587" y="189">Issues</tspan></text>
  </g>

  <g class="node">
    <circle class="node-circle" cx="821" cy="228" r="99"/>
    <text class="node-label"><tspan x="821" y="216">Process</tspan><tspan x="821" y="255">Issues</tspan></text>
  </g>

  <g class="node">
    <circle class="node-circle" cx="946" cy="443" r="99"/>
    <text class="node-label"><tspan x="950" y="429">Forecasting</tspan><tspan x="950" y="468">and Planning</tspan></text>
  </g>

  <g class="node">
    <circle class="node-circle" cx="904" cy="688" r="99"/>
    <text class="node-label"><tspan x="906" y="674">Customer</tspan><tspan x="906" y="713">Management</tspan></text>
  </g>

  <g class="node">
    <circle class="node-circle" cx="713" cy="850" r="99"/>
    <text class="node-label"><tspan x="713" y="834">SKU</tspan><tspan x="713" y="873">Complexity</tspan></text>
  </g>

  <g class="node">
    <circle class="node-circle" cx="465" cy="850" r="99"/>
    <text class="node-label"><tspan x="465" y="834">Supplier</tspan><tspan x="465" y="873">Management</tspan></text>
  </g>

  <g class="node">
    <circle class="node-circle" cx="273" cy="690" r="99"/>
    <text class="node-label"><tspan x="273" y="679">KPIs and</tspan><tspan x="273" y="718">Measures</tspan></text>
  </g>

  <g class="node">
    <circle class="node-circle" cx="229" cy="446" r="99"/>
    <text class="node-label"><tspan x="228" y="417">IT Systems</tspan><tspan x="228" y="456">and</tspan><tspan x="228" y="495">Information</tspan></text>
  </g>

  <g class="node">
    <circle class="node-circle" cx="354" cy="229" r="99"/>
    <text class="node-label"><tspan x="352" y="216">Terms and</tspan><tspan x="352" y="255">Conditions</tspan></text>
  </g>
</svg>
</body>
</html>
```